TALMORK

The business want a professional looking business card. We have a scetch we will add but want the extra upgrade, and would like more suggestions for variations of our business cards.

```html
<!DOCTYPE html>
<html lang="en">
<head>
<meta charset="utf-8">
<title>TALMORK — Business Card</title>
<link rel="stylesheet" href="https://fonts.googleapis.com/css2?family=Yeseva+One&family=Playfair+Display:wght@700&family=Lato:wght@400;700&display=swap">
<style>
  :root {
    --backdrop: #8f8f8f;
    --ink: #0a0a0a;
    --black-top: #0b0b0b;
    --black-mid: #222222;
    --black-bottom: #040404;
    --gold: #d9b25a;
    --gold-light: #f3dc98;
    --gold-deep: #5a3f17;
    --gold-mid: #b48a3a;
    --text-light: #e6e6e6;
  }
  * { box-sizing: border-box; margin: 0; padding: 0; }
  html, body {
    width: 1200px; height: 1200px; overflow: hidden;
    background: var(--backdrop);
  }
  .sheet { position: relative; width: 1200px; height: 1200px; }

  .card {
    position: absolute;
    left: 281px;
    width: 641px;
    height: 366px;
    border-radius: 18px;
    overflow: hidden;
  }

  /* Front */
  .card--front {
    top: 195px;
    background: linear-gradient(180deg, var(--black-top) 0%, var(--black-mid) 42%, var(--black-bottom) 100%);
  }
  .holder-name {
    position: absolute; left: 49px; top: 50px;
    font-family: "Yeseva One", serif;
    font-size: 23px;
    color: var(--gold);
    letter-spacing: 0.2px;
  }
  .holder-role {
    position: absolute; left: 50px; top: 86px;
    font-family: "Lato", sans-serif;
    font-size: 15px;
    color: var(--text-light);
  }
  .contact-list {
    position: absolute; left: 50px; top: 231px;
    list-style: none;
    font-family: "Lato", sans-serif;
    font-size: 14px;
    color: var(--text-light);
  }
  .contact-list li {
    display: flex; align-items: center;
    height: 22.5px;
  }
  .contact-list svg { width: 13px; height: 13px; margin-right: 10px; flex: none; }

  .brand {
    position: absolute; left: 395px; top: 225px;
    width: 250px;
    text-align: center;
  }
  .brand-name {
    font-family: "Playfair Display", serif;
    font-weight: 700;
    font-size: 44px;
    line-height: 1;
    color: var(--gold);
    letter-spacing: 1px;
  }
  .brand-tagline {
    margin-top: 10px;
    font-family: "Lato", sans-serif;
    font-size: 13px;
    letter-spacing: 6px;
    color: var(--gold);
    padding-left: 6px;
  }

  /* Back */
  .card--back {
    top: 639px;
  }
  .back-pattern {
    position: absolute; inset: 0;
    background: linear-gradient(180deg, var(--gold-deep) 0%, var(--gold-mid) 28%, var(--gold-light) 50%, var(--gold-mid) 72%, var(--gold-deep) 100%);
  }
  .back-mark {
    position: absolute; left: 0; right: 0; top: 123px;
    text-align: center;
  }
  .back-name {
    font-family: "Playfair Display", serif;
    font-weight: 700;
    font-size: 78px;
    line-height: 1;
    color: var(--ink);
    letter-spacing: 2px;
  }
  .back-tagline {
    margin-top: 14px;
    display: flex; align-items: center; justify-content: center;
    font-family: "Lato", sans-serif;
    font-size: 23px;
    letter-spacing: 9px;
    color: var(--ink);
  }
  .back-tagline .rule {
    width: 68px; height: 2px; background: var(--ink);
  }
  .back-tagline span.text { margin: 0 8px 0 17px; }
</style>
</head>
<body>
<main class="sheet">

  <section class="card card--front" aria-label="Business card front">
    <h1 class="holder-name">Aksel Brenne Holmvik</h1>
    <p class="holder-role">CEO &amp; Founder</p>

    <ul class="contact-list">
      <li>
        <svg viewBox="0 0 16 16" aria-hidden="true"><path fill="var(--gold)" d="M3.5 1.5l2.2 2.6-1.3 1.6c.8 1.9 2.2 3.3 4.1 4.2l1.6-1.3 2.6 2.2-1.5 2.2C6.5 12.6 3.4 9.5 1.4 3l2.1-1.5z"/></svg>
        004755501234
      </li>
      <li>
        <svg viewBox="0 0 16 16" aria-hidden="true"><rect x="1.5" y="3.5" width="13" height="9" fill="var(--gold)"/><path d="M1.5 3.5l6.5 5 6.5-5" fill="none" stroke="#111" stroke-width="1.2"/></svg>
        talmork.llc@postmail.com
      </li>
      <li>
        <svg viewBox="0 0 16 16" aria-hidden="true"><circle cx="8" cy="8" r="6.5" fill="var(--gold)"/><path d="M1.5 8h13M8 1.5c-2.5 3-2.5 10 0 13M8 1.5c2.5 3 2.5 10 0 13" fill="none" stroke="#111" stroke-width="0.9"/></svg>
        www.talmork.llc
      </li>
    </ul>

    <div class="brand">
      <div class="brand-name">TALMORK</div>
      <div class="brand-tagline">SINCE 2026</div>
    </div>
  </section>

  <section class="card card--back" aria-label="Business card back">
    <div class="back-pattern" role="img" aria-label="Gold metallic background with a repeating floral ornament pattern"></div>
    <div class="back-mark">
      <div class="back-name">TALMORK</div>
      <div class="back-tagline">
        <span class="rule"></span>
        <span class="text">SINCE 2026</span>
        <span class="rule"></span>
      </div>
    </div>
  </section>

</main>
</body>
</html>
```